Harborline Auto LLC

Car Dealer Customer Service
Address: 2874 Cresthaven Road, Shelbyville, TN 37162
web: www.harborlineautoxq.net
email: harborlineautoxq@mailnest.example
Phone: (931) 555-0148
Phone: (629) 555-0173

```html
<!DOCTYPE html>
<html lang="en">
<head>
<meta charset="utf-8">
<title>Harborline Auto – Business Card</title>
<link rel="stylesheet" href="https://fonts.googleapis.com/css2?family=Montserrat:wght@400;800&family=Oswald:wght@500&family=Arimo:wght@400&display=swap">
<style>
  :root {
    --bg: #2a2a2c;
    --blue-light: #2a8fcb;
    --blue-dark: #1c74a6;
    --gold: #ecb54a;
    --white: #ffffff;
    --ink: #111111;
  }
  * { box-sizing: border-box; margin: 0; padding: 0; }
  html, body { width: 1200px; height: 1015px; overflow: hidden; background: var(--bg); }
  .canvas { position: relative; width: 1200px; height: 1015px; }
  .card {
    position: absolute; left: 150px; width: 900px; height: 450px; overflow: hidden;
    background: linear-gradient(180deg, var(--blue-light), var(--blue-dark));
    box-shadow: 0 10px 30px rgba(0,0,0,.55);
  }
  .card--front { top: 38px; }
  .card--back { top: 527px; }

  /* Front */
  .front-band {
    position: absolute; left: 0; right: 0; top: 245px; height: 120px; background: var(--gold);
  }
  .front-title {
    position: absolute; left: 70px; top: 170px;
    font: 800 52px/1 "Montserrat", sans-serif; letter-spacing: 3px; color: var(--white);
  }
  .front-services {
    position: absolute; left: 110px; top: 262px;
    font: 500 38px/1.15 "Oswald", sans-serif; color: var(--white); text-transform: uppercase;
  }
  .front-services span { display: block; }
  .front-services span + span { padding-left: 30px; }

  /* Back */
  .back-mark {
    position: absolute; left: 240px; top: 22px; width: 150px; height: 150px;
    border-radius: 50%; background: var(--white);
  }
  .back-title {
    position: absolute; left: 250px; top: 185px;
    font: 800 50px/1 "Montserrat", sans-serif; letter-spacing: 3px; color: var(--white);
  }
  .back-band {
    position: absolute; left: 0; right: 0; top: 255px; height: 125px; background: var(--gold);
  }
  .person {
    position: absolute; right: 480px; top: 30px; text-align: right; color: var(--white);
  }
  .person-name { font: 800 28px/1 "Montserrat", sans-serif; letter-spacing: 1px; }
  .person-role { font: 400 19px/1.2 "Arimo", sans-serif; margin-top: 4px; }
  .divider {
    position: absolute; left: 440px; top: 14px; width: 1px; height: 98px; background: var(--white); opacity: .8;
  }
  .contacts {
    position: absolute; left: 462px; top: 14px; list-style: none; color: var(--white);
    font: 400 18px/1.35 "Arimo", sans-serif;
  }
  .contacts li { display: flex; align-items: center; gap: 10px; }
  .contacts svg { width: 16px; height: 16px; flex: none; }
  .address-strip {
    position: absolute; left: 0; right: 0; top: 380px; height: 52px; background: var(--white);
    display: flex; align-items: center; justify-content: center;
    font: 400 24px/1 "Arimo", sans-serif; color: var(--ink); letter-spacing: .5px;
  }
  .base-line { position: absolute; top: 432px; height: 18px; }
  .base-line--blue { left: 0; width: 520px; background: var(--blue-light); }
  .base-line--gold { left: 520px; right: 0; background: var(--gold); }
</style>
</head>
<body>
<main class="canvas">
  <section class="card card--front" aria-label="Card front">
    <div class="front-band"></div>
    <h1 class="front-title">HARBORLINE AUTO</h1>
    <p class="front-services"><span>Car Dealer</span><span>Customer Service</span></p>
  </section>

  <section class="card card--back" aria-label="Card back">
    <div class="back-mark" aria-hidden="true"></div>
    <h2 class="back-title">HARBORLINE AUTO</h2>
    <div class="back-band">
      <div class="person">
        <p class="person-name">MARCUS DELANEY</p>
        <p class="person-role">Managing Director</p>
      </div>
      <div class="divider"></div>
      <ul class="contacts">
        <li><svg viewBox="0 0 16 16" fill="none" stroke="#fff" stroke-width="1.6"><path d="M3 2l3 1 .5 3-1.5 1a8 8 0 004 4l1-1.5 3 .5 1 3-2 1C7 14 2 9 2 4z"/></svg>(931) 555-0148</li>
        <li><svg viewBox="0 0 16 16" fill="none" stroke="#fff" stroke-width="1.6"><path d="M3 2l3 1 .5 3-1.5 1a8 8 0 004 4l1-1.5 3 .5 1 3-2 1C7 14 2 9 2 4z"/></svg>(629) 555-0173</li>
        <li><svg viewBox="0 0 16 16" fill="none" stroke="#fff" stroke-width="1.4"><circle cx="8" cy="8" r="6.5"/><ellipse cx="8" cy="8" rx="3" ry="6.5"/><path d="M1.5 8h13M2.5 5h11M2.5 11h11"/></svg>www.harborlineautoxq.net</li>
        <li><svg viewBox="0 0 16 16" fill="none" stroke="#fff" stroke-width="1.4"><rect x="1.5" y="3.5" width="13" height="9"/><path d="M1.5 3.5L8 9l6.5-5.5"/></svg>harborlineautoxq@mailnest.example</li>
      </ul>
    </div>
    <p class="address-strip">2874 Cresthaven Road, Shelbyville, TN 37162</p>
    <div class="base-line base-line--blue"></div>
    <div class="base-line base-line--gold"></div>
  </section>
</main>
</body>
</html>
```